bean bag mailer

We manufacture bean bag chairs in Dallas. We want to send out a mailer to all of the daycares and churches in Dallas and surrounding areas. Summer time is very busy for these daycares, and we would like to offer fun, functional, and affordable furniture for them to use. We want the postcard to be very bright and attractive to kids.

Target Market(s)

We're targeting daycares and churches

Industry/Entity Type

Manufacture

Requirements
Must have
• We want the logo. We also want the phone number, which is 214-736-4819. We offer bulk discounts such as 5% off orders of at least 15. 10% off orders of at least 25. 20% off orders of at least 50. We would also like to note that these bags are made in the U.S.A.
Nice to have
• Want the postcard to be really bright, colorful, and eye-catching. The pics of the bean bags are just examples, other images can be used if they better fit the layout.

```html
<!DOCTYPE html>
<html lang="en">
<head>
<meta charset="utf-8">
<title>Lonestar Bean Bags – Postcard Mailer</title>
<link rel="stylesheet" href="https://fonts.googleapis.com/css2?family=Anton&family=Arimo:wght@400;700&family=Tinos&display=swap">
<style>
  :root {
    --stage: #0d0f0e;
    --white: #ffffff;
    --ink: #111111;
    --red: #c8242b;
    --sun: #f6e93a;
    --cream: #fdf27a;
    --mint: #e8f3e4;
    --leaf: #5ab43a;
    --orange: #f7941d;
    --orange-deep: #f26a1b;
    --sky: #29abe2;
    --grass: #39b54a;
    --row-yellow: #fff08a;
    --row-green: #8fcf7a;
    --row-pink: #f2b6d3;
    --row-blue: #8fd3ea;
    --row-orange: #ffc27a;
    --line: #6b6b6b;
  }
  * { margin: 0; padding: 0; box-sizing: border-box; }
  html, body { width: 1200px; height: 915px; overflow: hidden; background: var(--stage); }
  body { position: relative; font-family: "Arimo", Arial, sans-serif; }

  .card { position: absolute; left: 300px; width: 558px; height: 433px; background: var(--white); overflow: hidden; }
  .card--front { top: 22px; }
  .card--back { top: 463px; }
  .card svg.backdrop { position: absolute; left: 0; top: 0; }

  .brand { position: absolute; font-family: "Arimo", Arial, sans-serif; font-weight: 700; color: var(--white);
           font-size: 22px; letter-spacing: 0.5px; display: flex; align-items: center; gap: 8px; white-space: nowrap; }
  .brand__dot { width: 16px; height: 16px; border-radius: 50%; background: var(--orange); }
  .brand-tag { position: absolute; border-radius: 16px;
               background: linear-gradient(90deg, #1f3fa8 0 33%, #1a1a1a 33% 66%, #d8202a 66%); }

  .product-photo { position: absolute; border-radius: 40px;
    background: radial-gradient(circle at 25% 25%, #5fc33f 0 18%, transparent 19%),
                radial-gradient(circle at 20% 65%, #5a2a9c 0 22%, transparent 23%),
                radial-gradient(circle at 65% 25%, #5ab6e8 0 18%, transparent 19%),
                radial-gradient(circle at 78% 62%, #d6202a 0 22%, transparent 23%),
                radial-gradient(circle at 45% 40%, #f4cf1a 0 20%, transparent 21%),
                radial-gradient(circle at 48% 75%, #e8177f 0 22%, transparent 23%); }

  .offer { position: absolute; right: 0; height: 64px; color: var(--white); text-align: center;
           border-radius: 6px 0 0 6px; }
  .offer__value { font-family: "Anton", Impact, sans-serif; font-size: 40px; line-height: 48px; }
  .offer__value span { color: var(--ink); font-size: 30px; }
  .offer__terms { font-size: 11.5px; letter-spacing: 0.4px; line-height: 12px; }
  .offer--orange { top: 100px; width: 200px; background: linear-gradient(90deg, var(--orange), var(--orange-deep)); }
  .offer--blue { top: 170px; width: 190px; background: var(--sky); height: 66px; }
  .offer--green { top: 240px; width: 182px; background: var(--grass); height: 66px; }

  .made-in { position: absolute; left: 40px; top: 374px; display: flex; align-items: flex-end; gap: 4px;
             font-family: "Anton", Impact, sans-serif; color: var(--ink); }
  .made-in__small { font-size: 12px; line-height: 12px; }
  .made-in__big { font-size: 30px; line-height: 30px; }

  .call { position: absolute; text-align: center; }
  .call__label { font-family: "Tinos", "Times New Roman", serif; color: var(--ink); }
  .call__number { font-family: "Arimo", Arial, sans-serif; font-weight: 700; color: var(--red); }
  .card--front .call { left: 253px; top: 348px; width: 290px; }
  .card--front .call__label { font-size: 27px; line-height: 28px; margin-left: 30px; }
  .card--front .call__number { font-size: 33px; line-height: 36px; display: flex; align-items: center; gap: 8px; justify-content: center; }
  .phone-icon { width: 22px; height: 26px; background: var(--ink); border-radius: 4px; display: inline-flex; align-items: center; justify-content: center; }

  .benefits { position: absolute; left: 0; top: 112px; width: 270px; list-style: none; }
  .benefits li { height: 15.7px; font-size: 13px; line-height: 15.7px; padding-left: 38px; position: relative; color: var(--ink); }
  .benefits li svg { position: absolute; left: 38px; top: 3px; }
  .benefits li { text-indent: 13px; }
  .benefits li:nth-child(1), .benefits li:nth-child(6) { background: var(--row-yellow); }
  .benefits li:nth-child(2) { background: var(--row-green); }
  .benefits li:nth-child(3) { background: var(--row-pink); }
  .benefits li:nth-child(4) { background: var(--row-blue); }
  .benefits li:nth-child(5) { background: var(--row-orange); }

  .back-panel { position: absolute; left: 0; top: 205px; width: 270px; height: 152px; background: var(--mint); }
  .pile-photo { position: absolute; left: 73px; top: 15px; width: 120px; height: 88px; border-radius: 14px;
    background: linear-gradient(180deg, #2f58a8 0 25%, #e28fb5 25% 55%, #d2374a 55%); }
  .card--back .call { left: 0; top: 106px; width: 270px; }
  .card--back .call__label { font-size: 21px; line-height: 20px; }
  .card--back .call__number { font-size: 24px; line-height: 24px; }

  .stamp-box { position: absolute; left: 453px; top: 36px; width: 64px; height: 72px; border: 1px solid #9a9a9a;
               font-size: 11.5px; color: #777; text-align: center; padding-top: 16px; line-height: 14px; }
  .address-line { position: absolute; left: 296px; width: 197px; border-top: 1px solid var(--line); }
</style>
</head>
<body>

<section class="card card--front" aria-label="Postcard front">
  <svg class="backdrop" width="558" height="433" viewBox="0 0 558 433" aria-hidden="true">
    <rect width="558" height="433" fill="var(--mint)"/>
    <path d="M0 0H558V40C430 80 300 20 170 50C100 66 40 60 0 55Z" fill="var(--sun)"/>
    <path d="M0 55C60 62 110 68 170 52C260 30 330 60 420 55V80C320 90 220 70 140 85C80 96 30 92 0 90Z" fill="var(--leaf)"/>
    <circle cx="470" cy="0" r="130" fill="var(--orange)"/>
    <circle cx="470" cy="0" r="100" fill="#fbc02d"/>
    <circle cx="60" cy="50" r="18" fill="#ffffff" opacity="0.4"/>
    <circle cx="450" cy="30" r="14" fill="#ffffff" opacity="0.5"/>
    <circle cx="480" cy="20" r="10" fill="#ffffff" opacity="0.5"/>
    <path d="M0 340C120 330 200 320 320 316C420 314 500 320 558 332V433H0Z" fill="var(--cream)"/>
    <path d="M0 340C120 330 200 320 320 316C420 314 500 320 558 332V338C500 326 420 322 320 324C200 328 120 338 0 350Z" fill="var(--ink)"/>
  </svg>

  <div class="brand" style="left:18px; top:66px;"><span class="brand__dot"></span>Lonestar Bean Bags</div>
  <div class="brand-tag" role="img" aria-label="Blue, black and red bean bags" style="left:290px; top:66px; width:88px; height:30px;"></div>

  <div class="product-photo" role="img" aria-label="Child sitting on a pink bean bag among green, purple, yellow, blue and red bean bags" style="left:15px; top:108px; width:375px; height:255px;"></div>

  <div class="offer offer--orange"><div class="offer__value">5%<span>OFF</span></div><div class="offer__terms">ON ORDERS ATLEAST 15</div></div>
  <div class="offer offer--blue"><div class="offer__value">10%<span>OFF</span></div><div class="offer__terms">ON ORDERS ATLEAST 25</div></div>
  <div class="offer offer--green"><div class="offer__value">20%<span>OFF</span></div><div class="offer__terms">ON ORDERS ATLEAST 50</div></div>

  <div class="made-in">
    <div class="made-in__small">MADE<br>IN THE</div>
    <div class="made-in__big">USA</div>
    <svg width="48" height="26" viewBox="0 0 48 26" aria-label="US flag" role="img">
      <rect width="48" height="26" fill="#fff"/>
      <g fill="#c8242b"><rect y="0" width="48" height="2"/><rect y="4" width="48" height="2"/><rect y="8" width="48" height="2"/><rect y="12" width="48" height="2"/><rect y="16" width="48" height="2"/><rect y="20" width="48" height="2"/><rect y="24" width="48" height="2"/></g>
      <rect width="20" height="14" fill="#2a3d8f"/>
    </svg>
  </div>

  <div class="call">
    <div class="call__label">CALL NOW</div>
    <div class="call__number">
      <span class="phone-icon"><svg width="12" height="18" viewBox="0 0 12 18" aria-hidden="true"><path d="M3 1h3l1 4-2 2c1 2 2 3 3 4l2-2 1 4v3c-6 0-10-7-10-13z" fill="#fff"/></svg></span>
      214-736-4819
    </div>
  </div>
</section>

<section class="card card--back" aria-label="Postcard back">
  <svg class="backdrop" width="558" height="433" viewBox="0 0 558 433" aria-hidden="true">
    <rect width="419" height="139" fill="var(--mint)"/>
    <path d="M0 0H419V20C320 50 220 10 120 35C70 46 30 44 0 40Z" fill="var(--sun)"/>
    <path d="M0 40C50 46 90 50 130 38C210 18 300 46 380 42V58C300 64 200 50 120 62C70 70 30 66 0 64Z" fill="var(--leaf)"/>
    <circle cx="360" cy="0" r="90" fill="var(--orange)"/>
    <circle cx="360" cy="0" r="68" fill="#fbc02d"/>
    <circle cx="100" cy="30" r="10" fill="#ffffff" opacity="0.5"/>
    <circle cx="340" cy="30" r="8" fill="#ffffff" opacity="0.5"/>
  </svg>

  <div class="brand" style="left:16px; top:72px;"><span class="brand__dot"></span>Lonestar Bean Bags</div>
  <div class="brand-tag" role="img" aria-label="Blue, black and red bean bags" style="left:308px; top:72px; width:92px; height:30px;"></div>

  <ul class="benefits">
    <li><svg width="10" height="10" viewBox="0 0 10 10" aria-hidden="true"><path d="M1 5l3 3 5-7" stroke="var(--red)" stroke-width="2" fill="none"/></svg>Alternative Furniture</li>
    <li><svg width="10" height="10" viewBox="0 0 10 10" aria-hidden="true"><path d="M1 5l3 3 5-7" stroke="var(--red)" stroke-width="2" fill="none"/></svg>Great Selection</li>
    <li><svg width="10" height="10" viewBox="0 0 10 10" aria-hidden="true"><path d="M1 5l3 3 5-7" stroke="var(--red)" stroke-width="2" fill="none"/></svg>Vivid Colors</li>
    <li><svg width="10" height="10" viewBox="0 0 10 10" aria-hidden="true"><path d="M1 5l3 3 5-7" stroke="var(--red)" stroke-width="2" fill="none"/></svg>Featuring High Quality Materials</li>
    <li><svg width="10" height="10" viewBox="0 0 10 10" aria-hidden="true"><path d="M1 5l3 3 5-7" stroke="var(--red)" stroke-width="2" fill="none"/></svg>Comfortable</li>
    <li><svg width="10" height="10" viewBox="0 0 10 10" aria-hidden="true"><path d="M1 5l3 3 5-7" stroke="var(--red)" stroke-width="2" fill="none"/></svg>Affordable Bean Bags</li>
  </ul>

  <div class="back-panel">
    <div class="pile-photo" role="img" aria-label="Pyramid of stacked colourful bean bags"></div>
    <div class="call">
      <div class="call__label">CALL NOW</div>
      <div class="call__number">214-736-4819</div>
    </div>
  </div>

  <div class="stamp-box">Place<br>Stamp<br>Here</div>
  <div class="address-line" style="top:219px;"></div>
  <div class="address-line" style="top:258px;"></div>
  <div class="address-line" style="top:299px;"></div>
</section>

</body>
</html>
```